Anzeigengestaltung für Heilpraktikerin für Psychotherapie
Hallo sulvarn, ich bin sehr zufrieden mit dem Design. Danke LG Margit Lohberg
Zielgruppe
Heilpraktikerin für Psychotherapie, Atem- und Körpertherapeutin, Einzelthearpie, Gruppentherapie, Menschen in Lebenskrisen; Menschen, die ihr Leben verändern wollen, Menschen suchen mehr Selbsterfahrung, vorwiegend Frauen, Atersgruppe 20 aufwärts, Menschen mit psychischen Problemen
Entspannung, Berühren, Massieren, Halten, Gespräch, Bewegen, Begleitung Während der Schwangerschaft, Geburt und danach, Trauerbegleitung
Aufgabenstellung
Name und Berufsbezeichnung sind mir wichtig
Praxiseröffnung, Termine nach Vereinbarung
aktuelles Angebot: Fantasiereise- Entspannung von Alltagsstress
sonstiges Angebot: Einzeltherapie/Gruppentherapie,

```html
<!DOCTYPE html>
<html lang="de">
<head>
<meta charset="utf-8">
<title>PraxisEck – Praxiseröffnung</title>
<link rel="stylesheet" href="https://fonts.googleapis.com/css2?family=Crimson+Pro:wght@400;600;700&display=swap">
<style>
  :root {
    --plum: #75295a;
    --plum-text: #6e2a57;
    --lavender-top: #e9deef;
    --lavender-mid: #c8b3d8;
    --lavender-low: #9a7fb6;
    --ground: #3e3149;
    --magenta: #e2137e;
    --white: #ffffff;
    --photo-tone: #b79a86;
  }
  html, body {
    margin: 0;
    padding: 0;
    overflow: hidden;
    background: #ffffff;
  }
  .ad {
    position: relative;
    width: 800px;
    height: 1200px;
    overflow: hidden;
    font-family: "Crimson Pro", Georgia, serif;
  }
  .ad__scene {
    position: absolute;
    inset: 0;
    background: linear-gradient(180deg,
      var(--lavender-top) 0%,
      #ddd0e6 35%,
      var(--lavender-mid) 62%,
      var(--lavender-low) 88%,
      var(--ground) 100%);
  }
  .ad__header {
    position: absolute;
    top: 0;
    left: 0;
    width: 800px;
    height: 68px;
    background: var(--plum);
  }
  .ad__header-text {
    position: absolute;
    right: 40px;
    top: 19px;
    margin: 0;
    color: var(--white);
    font-size: 24px;
    font-weight: 400;
    letter-spacing: 0.2px;
  }
  .ad__portrait {
    position: absolute;
    left: 34px;
    top: 19px;
    width: 128px;
    height: 160px;
    background: linear-gradient(160deg, #9c8066 0%, var(--photo-tone) 55%, #4a3a35 100%);
  }
  .ad__brand {
    position: absolute;
    top: 255px;
    left: 0;
    width: 800px;
    text-align: center;
    margin: 0;
    color: var(--plum-text);
    font-size: 46px;
    font-weight: 600;
  }
  .ad__title {
    position: absolute;
    left: 66px;
    top: 352px;
    margin: 0;
    color: var(--plum-text);
    font-size: 88px;
    font-weight: 400;
    letter-spacing: 1px;
    line-height: 1;
  }
  .ad__contact {
    position: absolute;
    left: 73px;
    top: 458px;
    margin: 0;
    color: var(--plum-text);
    font-size: 27px;
    line-height: 38px;
    font-style: normal;
  }
  .ad__badge {
    position: absolute;
    left: 94px;
    top: 866px;
    width: 272px;
    height: 272px;
    border-radius: 50%;
    background: var(--magenta);
    color: var(--white);
    text-align: center;
  }
  .ad__badge-label {
    margin: 48px 0 4px;
    font-size: 23px;
    line-height: 1.1;
  }
  .ad__badge-offer {
    margin: 0;
    font-size: 39px;
    font-weight: 700;
    line-height: 0.98;
  }
  .ad__footer {
    position: absolute;
    right: 42px;
    bottom: 24px;
    margin: 0;
    color: var(--white);
    font-size: 29px;
  }
</style>
</head>
<body>
  <main class="ad">
    <div class="ad__scene" role="img" aria-label="Foto: Silhouette einer Frau mit ausgebreiteten Armen auf einer Wiese vor violettem Himmel"></div>

    <header class="ad__header">
      <p class="ad__header-text">Margit Lohberg &nbsp;·&nbsp; Heilpraktikerin für Psychotherapie</p>
    </header>
    <div class="ad__portrait" role="img" aria-label="Porträtfoto der Heilpraktikerin"></div>

    <p class="ad__brand">PraxisEck</p>

    <h1 class="ad__title">Praxiseröffnung</h1>
    <address class="ad__contact">
      Lindenweg 14 / 72999 Talheim<br>
      praxiseck.margitlohberg@gmail.com<br>
      01705550192 / www.praxiseck.org
    </address>

    <div class="ad__badge">
      <p class="ad__badge-label">aktuelles Angebot:</p>
      <p class="ad__badge-offer">Fantasiereise-<br>Entspannung<br>vom Alltags-<br>stress</p>
    </div>

    <p class="ad__footer">Termine nach Vereinbarung</p>
  </main>
</body>
</html>
```